VELMOR Website Design

We need a website designed for our company VELMOR. We are a luxury lifestyle club that will provide benefits and services for our members. The site should be clean & sleek, preferably using black and white (or darker colors). (example sites: stravenhall.example, plinth.example)

Here is a link of a sample page I did using wix. (https://dunmere7.sitehostly.example/mysite) This can be used to get a general idea.

Target Market(s)

Upper Middle Class in the United States

Number of Pages Required

5+ page

Font styles to use
Sans Serif
Other font styles liked:
• Arial (or other similar fonts)

Requirements
Must have
• A clean design that is eye-catching and speaks to our company.
Nice to have
• Ideas for copy.

```html
<!DOCTYPE html>
<html lang="en">
<head>
<meta charset="utf-8">
<title>VELMOR — A Members Only Lifestyle Club</title>
<link rel="stylesheet" href="https://fonts.googleapis.com/css2?family=Poppins:wght@300;400;500;600&display=swap">
<style>
:root{
  --black:#000;
  --ink:#111;
  --white:#fff;
  --paper:#efefef;
  --muted:#bdbdbd;
  --line:#3a3a3a;
  --hero-a:#2a1a1c;
  --hero-b:#5a3a36;
  --band-a:#2b1c12;
  --band-b:#4a3220;
}
*{margin:0;padding:0;box-sizing:border-box}
html,body{width:1200px;height:2791px;overflow:hidden}
body{position:relative;background:var(--black);font-family:"Poppins",Arial,sans-serif;color:var(--ink)}
.abs{position:absolute}
.bands{position:absolute;left:0;top:0}
.center{left:0;width:1200px;text-align:center}

/* nav */
.nav{left:0;top:0;width:1200px;height:48px;background:var(--black);color:var(--white)}
.brand{left:160px;top:9px;font-size:25px;font-weight:400;letter-spacing:1px}
.menu{left:425px;top:16px;display:flex;gap:30px;font-size:12.5px}
.account{left:893px;top:18px;font-size:12px;color:var(--muted);letter-spacing:.3px}
.account span{margin:0 12px}

/* hero */
.hero-title{top:250px;font-size:44px;font-weight:400;color:var(--white);letter-spacing:.5px}
.btn{display:flex;align-items:center;justify-content:center;font-size:15px;font-weight:600;letter-spacing:.5px}
.btn-light{background:var(--white);color:var(--black)}
.btn-dark{background:var(--black);color:var(--white)}
.dots{left:512px;top:556px;display:flex;gap:4px}
.dots i{display:block;width:41px;height:4px;background:var(--white)}
.dots i.off{background:transparent;border:1px solid var(--white)}

/* about */
.about-title{left:160px;top:772px;font-size:34px;font-weight:400;color:var(--ink)}
.copy{font-size:12.3px;line-height:24px;color:#222}
.photo-frame{left:666px;top:722px;width:370px;height:465px;background:var(--white);padding:9px}

/* sections */
.section-title{font-size:34px;font-weight:400}
.lede{font-size:13.5px;line-height:24px}
.service{top:1419px;width:228px;text-align:center;color:var(--white)}
.service .ring{width:94px;height:94px;margin:0 auto;display:block}
.service h3{margin-top:22px;font-size:17px;font-weight:400}
.service p{margin-top:12px;font-size:11.5px;line-height:20px}

/* footer */
.social{top:2580px;left:495px;display:flex;gap:7px}
.social i{display:block;width:48px;height:48px;border:2px solid var(--white);border-radius:50%}
.contact{top:2676px;font-size:12.5px;line-height:19px;color:var(--white)}
.rule{left:223px;top:2736px;width:661px;height:1px;background:var(--line)}
.legal{top:2752px;font-size:11.5px;color:var(--white)}
</style>
</head>
<body>

<!-- background bands -->
<svg class="bands" width="1200" height="2791" viewBox="0 0 1200 2791" aria-hidden="true">
  <rect x="0" y="0" width="1200" height="2791" fill="var(--black)"/>
  <polygon points="0,595 1200,595 1200,2524 0,2524" fill="var(--paper)"/>
  <polygon points="0,1276 1200,1075 1200,2154 0,2292" fill="var(--black)"/>
  <polygon points="0,2292 1200,2154 1200,2502 0,2524" fill="var(--white)"/>
  <polygon points="0,2524 1200,2490 1200,2791 0,2791" fill="#2a2a2a"/>
  <polygon points="0,2528 1200,2508 1200,2791 0,2791" fill="var(--black)"/>
</svg>

<svg class="abs" style="left:0;top:0" width="1200" height="700" viewBox="0 0 1200 700" role="img" aria-label="Photo of friends laughing and toasting with drinks at a dimly lit club">
  <defs>
    <radialGradient id="heroGlow" cx="0.5" cy="0.4" r="0.75">
      <stop offset="0" stop-color="var(--hero-b)"/>
      <stop offset="1" stop-color="var(--hero-a)"/>
    </radialGradient>
  </defs>
  <polygon points="0,0 1200,0 1200,595 0,700" fill="url(#heroGlow)"/>
</svg>

<svg class="abs" style="left:0;top:1652px" width="1200" height="640" viewBox="0 0 1200 640" role="img" aria-label="Photo of members celebrating together at a party">
  <defs>
    <linearGradient id="bandGlow" x1="0" y1="0" x2="1" y2="1">
      <stop offset="0" stop-color="var(--band-a)"/>
      <stop offset="0.5" stop-color="var(--band-b)"/>
      <stop offset="1" stop-color="#1a120c"/>
    </linearGradient>
  </defs>
  <polygon points="0,134 1200,0 1200,502 0,640" fill="url(#bandGlow)"/>
</svg>

<!-- navigation -->
<header class="abs nav">
  <div class="abs brand">VELMOR</div>
  <nav class="abs menu"><span>Home</span><span>About</span><span>Services and Benefits</span><span>Apply</span><span>Contact</span></nav>
  <div class="abs account">VISIT A CLUB<span>|</span>LOG IN</div>
</header>

<!-- hero -->
<h1 class="abs center hero-title">A MEMBERS ONLY LIFESTYLE CLUB</h1>
<div class="abs btn btn-light" style="left:452px;top:335px;width:145px;height:45px">JOIN NOW</div>
<div class="abs btn btn-dark" style="left:601px;top:335px;width:147px;height:45px">VISIT A CLUB</div>
<div class="abs dots"><i></i><i></i><i class="off"></i><i></i></div>

<!-- about -->
<h2 class="abs about-title">About VELMOR</h2>
<p class="abs copy" style="left:160px;top:838px;width:470px">VELMOR is a members only lifestyle club founded in order to bring the best services, experiences, and opportunities to our diverse community of members. Our members consist of creatives, athletes, artists, and other professionals.</p>
<p class="abs copy" style="left:160px;top:934px;width:470px">Sed ut perspiciatis unde omnis iste natus error sit voluptatem accusantium doloremq ue laudantium, totam rem aperiam, eaque ipsa quae ab illo inventore veritatis et quasi architecto beatae vitae dicta sunt explicabo. Nemo enim ipsam voluptatem quia vol uptas sit aspe ut perspiciatis unde omnis iste natus error sit voluptatem accusantium doloremque laudantium, totam rem aperiam, eaque ipsa quae ab illo inventore veritatis et quasi architecto beatae vitae dicta sunt explicabo.</p>
<div class="abs btn btn-dark" style="left:160px;top:1099px;width:112px;height:34px;font-size:12px">READ MORE</div>
<div class="abs photo-frame">
  <svg width="352" height="447" viewBox="0 0 352 447" role="img" aria-label="Photo of three friends sharing drinks on a rooftop sofa under party bunting">
    <defs><linearGradient id="aboutPhoto" x1="0" y1="0" x2="0" y2="1"><stop offset="0" stop-color="#c9ccd0"/><stop offset="0.5" stop-color="#7d8a86"/><stop offset="1" stop-color="#2f4a45"/></linearGradient></defs>
    <rect width="352" height="447" fill="url(#aboutPhoto)"/>
  </svg>
</div>

<!-- benefits -->
<h2 class="abs center section-title" style="top:1258px;color:var(--white)">Benefits and Services</h2>
<p class="abs center lede" style="top:1316px;color:var(--white)">Sed ut perspiciatis unde omnis iste natus error sit voluptatem accusantium doloremque laudantium,<br>totam rem aperiam, eaque ipsa qute natus error sit voluptaae ab illo inventore ver</p>

<svg class="abs" style="left:114px;top:1444px" width="24" height="44" viewBox="0 0 24 44" aria-hidden="true"><polyline points="20,2 4,22 20,42" fill="none" stroke="#444" stroke-width="2"/></svg>
<svg class="abs" style="left:1066px;top:1444px" width="24" height="44" viewBox="0 0 24 44" aria-hidden="true"><polyline points="4,2 20,22 4,42" fill="none" stroke="#444" stroke-width="2"/></svg>

<div class="abs service" style="left:143px">
  <svg class="ring" viewBox="0 0 94 94" aria-hidden="true"><circle cx="47" cy="47" r="45" fill="none" stroke="var(--white)" stroke-width="2"/><rect x="30" y="27" width="34" height="40" fill="none" stroke="var(--white)" stroke-width="2"/><line x1="36" y1="35" x2="58" y2="35" stroke="var(--white)" stroke-width="2"/><circle cx="43" cy="52" r="7" fill="none" stroke="var(--white)" stroke-width="2"/><line x1="54" y1="45" x2="58" y2="45" stroke="var(--white)" stroke-width="2"/><line x1="54" y1="52" x2="58" y2="52" stroke="var(--white)" stroke-width="2"/><line x1="54" y1="59" x2="58" y2="59" stroke="var(--white)" stroke-width="2"/></svg>
  <h3>Accounting Services</h3>
  <p>Sed ut perspiciatis unde otsitv olul optatem accusan tium dolore loreue laudlorem ipspta te iu doorl.</p>
</div>
<div class="abs service" style="left:372px">
  <svg class="ring" viewBox="0 0 94 94" aria-hidden="true"><circle cx="47" cy="47" r="45" fill="none" stroke="var(--white)" stroke-width="2"/><circle cx="50" cy="36" r="11" fill="none" stroke="var(--white)" stroke-width="2"/><path d="M28 58 L40 52 L56 55 L66 50 M40 66 L56 62 L68 54" fill="none" stroke="var(--white)" stroke-width="2"/></svg>
  <h3>Investment Services</h3>
  <p>Sed ut perspiciatis unde otsitv olul optatem accusan tium dolore loreue laudlorem ipspta te iu doorl.</p>
</div>
<div class="abs service" style="left:600px">
  <svg class="ring" viewBox="0 0 94 94" aria-hidden="true"><circle cx="47" cy="47" r="45" fill="none" stroke="var(--white)" stroke-width="2"/><path d="M32 66 L42 36 L60 56 Z" fill="none" stroke="var(--white)" stroke-width="2"/><line x1="52" y1="32" x2="56" y2="26" stroke="var(--white)" stroke-width="2"/><line x1="60" y1="38" x2="68" y2="34" stroke="var(--white)" stroke-width="2"/><circle cx="64" cy="26" r="2" fill="var(--white)"/></svg>
  <h3>Private Events</h3>
  <p>Sed ut perspiciatis unde otsitv olul optatem accusan tium dolore loreue laudlorem ipspta te iu doorl.</p>
</div>
<div class="abs service" style="left:829px">
  <svg class="ring" viewBox="0 0 94 94" aria-hidden="true"><circle cx="47" cy="47" r="45" fill="none" stroke="var(--white)" stroke-width="2"/><rect x="36" y="26" width="22" height="42" fill="none" stroke="var(--white)" stroke-width="2"/><rect x="28" y="44" width="8" height="24" fill="none" stroke="var(--white)" stroke-width="2"/><rect x="58" y="40" width="9" height="28" fill="none" stroke="var(--white)" stroke-width="2"/><line x1="41" y1="34" x2="53" y2="34" stroke="var(--white)" stroke-width="2"/><line x1="41" y1="42" x2="53" y2="42" stroke="var(--white)" stroke-width="2"/><line x1="41" y1="50" x2="53" y2="50" stroke="var(--white)" stroke-width="2"/></svg>
  <h3>Real Estate Services</h3>
  <p>Sed ut perspiciatis unde otsitv olul optatem accusan tium dolore loreue laudlorem ipspta te iu doorl.</p>
</div>

<!-- referral band -->
<h2 class="abs center section-title" style="top:1880px;color:var(--white)">Sed ut perspiciatis unde omnis</h2>
<p class="abs center lede" style="top:1938px;color:var(--white)">Sed ut perspiciatis unde omnis iste natus error sit voluptatem accusantium doloremque laudantium,<br>totam rem aperiam, eaque ipsa qute natus error sit voluptaae ab illo inventore ver</p>
<div class="abs btn btn-light" style="left:519px;top:2003px;width:162px;height:45px">REFER A FRIEND</div>

<!-- experiences -->
<h2 class="abs center section-title" style="top:2300px;color:var(--ink)">Experiences</h2>
<p class="abs center lede" style="top:2358px;color:var(--ink)">Sed ut perspiciatis unde omnis iste natus error sit voluptatem accusantium doloremque laudantium,<br>totam rem aperiam, eaque ipsa qute natus error sit voluptaae ab illo inventore ver</p>
<div class="abs btn btn-dark" style="left:519px;top:2424px;width:162px;height:45px">FIND A CLUB</div>

<!-- footer -->
<footer>
  <div class="abs social"><i></i><i></i><i></i><i></i></div>

  <svg class="abs" style="left:282px;top:2678px" width="20" height="24" viewBox="0 0 20 24" aria-hidden="true"><path d="M10 22 C4 14 2 11 2 8 A8 8 0 0 1 18 8 C18 11 16 14 10 22 Z" fill="none" stroke="var(--white)" stroke-width="1.5"/><circle cx="10" cy="8" r="3" fill="none" stroke="var(--white)" stroke-width="1.5"/></svg>
  <div class="abs contact" style="left:320px">412 Harlow Crescent,<br>Brindle Quay, Ostvale</div>

  <svg class="abs" style="left:478px;top:2678px" width="24" height="24" viewBox="0 0 24 24" aria-hidden="true"><path d="M5 2 L9 2 L11 7 L8 9 C9 12 12 15 15 16 L17 13 L22 15 L22 19 C22 21 20 22 18 22 C9 21 3 15 2 6 C2 4 3 2 5 2 Z" fill="none" stroke="var(--white)" stroke-width="1.5"/></svg>
  <div class="abs contact" style="left:521px">8 800 314 772 09<br>8 800 462 118 53</div>

  <svg class="abs" style="left:652px;top:2681px" width="26" height="18" viewBox="0 0 26 18" aria-hidden="true"><rect x="1" y="1" width="24" height="16" fill="none" stroke="var(--white)" stroke-width="1.5"/><polyline points="1,1 13,10 25,1" fill="none" stroke="var(--white)" stroke-width="1.5"/></svg>
  <div class="abs contact" style="left:696px">hello@velmor.example<br>founder@velmor.example</div>

  <div class="abs rule"></div>
  <p class="abs center legal">© 2018 VELMOR.All rights are reserved. Privacy | Terms of use</p>
</footer>

</body>
</html>
```